Business Card for: Bramwell Financial Advisory Services Inc.

provide strategic financial advisory services to companies in the areas of corporate finance, mergers and acquisitions, executive coaching and strategic planning

Target Market(s)

Companies, banks, accountants, lawyers

Industry/Entity Type

High end business consulting in corporate finance, mergers and acquisitions, consulting

Contact Information for Business Card

Name of company, Name: xxxxxx xxxxxx , CEO, - phone number: 1-xxx-xxx-xxxx, - email address,

Requirements
Must have
• Must be professional and simple.
Nice to have
• simple, straight graphics, must give the impression that we are trustworthy, professional, competent
Should not have
• loud colors, loud design features

```html
<!DOCTYPE html>
<html lang="en">
<head>
<meta charset="utf-8">
<title>Bramwell Financial Advisory – Business Card</title>
<link href="https://fonts.googleapis.com/css2?family=Montserrat:wght@400;500;700&display=swap" rel="stylesheet">
<style>
  :root {
    --bg: #bdbdbd;
    --blue-deep: #0677b8;
    --blue-mid: #1598cf;
    --blue-light: #4cc6e4;
    --ink: #2b2b2b;
    --ink-soft: #6d6d6d;
    --white: #ffffff;
    --pale: #eaf4fa;
  }
  * { box-sizing: border-box; margin: 0; padding: 0; }
  html, body { width: 1200px; height: 900px; overflow: hidden; }
  body {
    position: relative;
    background: var(--bg);
    font-family: "Montserrat", sans-serif;
  }
  .card {
    position: absolute;
    width: 630px;
    height: 360px;
    border-radius: 26px;
    overflow: hidden;
  }

  /* Front */
  .card-front {
    left: 110px; top: 80px;
    background: linear-gradient(180deg, var(--blue-mid) 0%, var(--blue-light) 42%, var(--blue-mid) 72%, var(--blue-deep) 100%);
    display: flex; flex-direction: column; align-items: center; justify-content: center;
    color: var(--white);
  }
  .front-brand { display: flex; align-items: center; gap: 16px; }
  .brand-dot {
    width: 34px; height: 34px; border-radius: 50%;
    background: var(--white);
  }
  .front-name { font-size: 64px; font-weight: 500; letter-spacing: 1px; line-height: 1; }
  .front-tagline { margin-top: 10px; font-size: 20px; font-weight: 400; letter-spacing: 1.5px; padding-left: 50px; }

  /* Back */
  .card-back {
    left: 460px; top: 470px;
    background: linear-gradient(90deg, var(--white) 55%, var(--pale) 100%);
    color: var(--ink);
  }
  .back-brand { position: absolute; left: 70px; top: 56px; display: flex; align-items: center; gap: 14px; }
  .back-brand .brand-dot { width: 30px; height: 30px; background: var(--blue-mid); }
  .back-name { font-size: 40px; font-weight: 500; color: var(--ink); line-height: 1; }
  .back-tagline { position: absolute; left: 114px; top: 104px; font-size: 13px; color: var(--ink-soft); letter-spacing: 1px; }

  .person { position: absolute; left: 110px; top: 160px; }
  .person-name { font-size: 30px; font-weight: 700; color: var(--ink); }
  .person-title { font-size: 18px; color: var(--ink-soft); margin-top: 2px; }

  .contacts { position: absolute; left: 110px; top: 244px; list-style: none; }
  .contacts li { display: flex; align-items: center; gap: 12px; font-size: 17px; color: var(--ink); height: 28px; }
  .icon { width: 22px; height: 22px; border-radius: 3px; display: flex; align-items: center; justify-content: center; }
  .icon-phone { background: var(--blue-light); }
  .icon-mail { background: var(--blue-mid); }
  .icon-web { background: var(--blue-deep); }

  .edge-bar {
    position: absolute; left: 0; top: 250px;
    width: 34px; height: 48px;
    background: linear-gradient(90deg, var(--blue-deep), var(--blue-light));
  }
</style>
</head>
<body>

  <section class="card card-front" aria-label="Business card front">
    <div class="front-brand">
      <span class="brand-dot"></span>
      <span class="front-name">Bramwell</span>
    </div>
    <p class="front-tagline">Financial Advisory Inc</p>
  </section>

  <section class="card card-back" aria-label="Business card back">
    <div class="edge-bar"></div>
    <div class="back-brand">
      <span class="brand-dot"></span>
      <span class="back-name">Bramwell</span>
    </div>
    <p class="back-tagline">Financial Advisory Inc</p>

    <div class="person">
      <p class="person-name">Elliot Marsh</p>
      <p class="person-title">Managing Director</p>
    </div>

    <ul class="contacts">
      <li>
        <span class="icon icon-phone">
          <svg width="14" height="14" viewBox="0 0 24 24" aria-hidden="true"><path fill="#fff" d="M6.6 10.8a15 15 0 0 0 6.6 6.6l2.2-2.2c.3-.3.7-.4 1-.2 1.1.4 2.3.6 3.6.6.6 0 1 .4 1 1V20c0 .6-.4 1-1 1A17 17 0 0 1 3 4c0-.6.4-1 1-1h3.5c.6 0 1 .4 1 1 0 1.3.2 2.5.6 3.6.1.3 0 .7-.2 1z"/></svg>
        </span>
        044-555 012 347
      </li>
      <li>
        <span class="icon icon-mail">
          <svg width="14" height="14" viewBox="0 0 24 24" aria-hidden="true"><rect x="2" y="5" width="20" height="14" rx="1" fill="none" stroke="#fff" stroke-width="2"/><path d="M2 6l10 7 10-7" fill="none" stroke="#fff" stroke-width="2"/></svg>
        </span>
        hello@bramwelladvisory.com
      </li>
      <li>
        <span class="icon icon-web">
          <svg width="14" height="14" viewBox="0 0 24 24" aria-hidden="true"><g fill="none" stroke="#fff" stroke-width="2"><circle cx="12" cy="12" r="9"/><path d="M3 12h18M12 3c3 3 3 15 0 18M12 3c-3 3-3 15 0 18"/></g></svg>
        </span>
        www.bramwelladvisory.com
      </li>
    </ul>
  </section>

</body>
</html>
```